Popup Nightclub Grand Opening Flyer

We need to design a flyer for the grand opening of an upscale, exclusive nightclub called "Lantern". The design needs to be chic and exclusive. The background should be black and the text should primarily be white. We like minimalist designs.

Here is the text for the flyer
-
Velvetroll Atlanta Presents

Lantern (LOGO)

A Popup Nightclub Experience
For one night Only

Friday, October 18, 2013
Party begins at 9PM

INVITE ONLY

See invitation for location details
(Velvetroll Atlanta logo)

-
Examples we like

http://cdn4-x.pressfolio-example.com/sites/default/files/styles/image_content_width/hash/3b/fd/2468013579_4421_flyer.jpg?itok=K9rtQw2z

http://files.hubspace-example.net/files/8Hqq-Tr72WWE3kaRbTmcxP5QZK2F396J8nbRw4CKMHfdX2Y7qSEF-MqjxDoNrLY3QCyQJD7npjGaRq3k-Mhx6hqf3MDSWf8r3/2zenSaturdays.jpg

http://morvex-example.com/wp-content/uploads/siteskin/widgetkit/gallery/2zen/2zen-gen_qstay4-01.jpg

Hi All, one thing that we are seeing that we don't like is on over emphasis on the phrase "a popup nightclub experience" please don't make this the largest thing on the flyer

Target Market(s)

Target market is 25-35 year olds who are affluent (rich) and like luxury brands

Requirements
Must have
• Dark Background
Nice to have
• Velvetroll Logo on the bottom
Modern text that isn't curvy
Should not have
• Curved text

```html
<!DOCTYPE html>
<html lang="en">
<head>
<meta charset="utf-8">
<title>Lantern — Velvetroll Atlanta Presents</title>
<link rel="stylesheet" href="https://fonts.googleapis.com/css2?family=Arimo:wght@400;700&family=Raleway:wght@300&display=swap">
<style>
  :root {
    --ink: #050505;
    --stripe-light: #2c2c2c;
    --stripe-dark: #0b0b0b;
    --white: #ffffff;
    --soft-white: #e6e6e6;
    --muted: #9c9c9c;
    --mark: #3a3a3a;
  }
  html, body {
    margin: 0;
    padding: 0;
    width: 827px;
    height: 1200px;
    overflow: hidden;
    background: var(--ink);
  }
  .flyer {
    position: relative;
    width: 827px;
    height: 1200px;
    overflow: hidden;
    font-family: "Arimo", Arial, sans-serif;
    color: var(--white);
  }
  .backdrop {
    position: absolute;
    inset: 0;
    background:
      radial-gradient(ellipse 70% 45% at 50% 38%, rgba(70,70,70,0.55), transparent 70%),
      linear-gradient(160deg, var(--stripe-dark) 0%, var(--stripe-light) 45%, var(--stripe-dark) 75%, #181818 100%);
  }
  .line-text {
    position: absolute;
    left: 0;
    width: 100%;
    margin: 0;
    text-align: center;
    text-transform: uppercase;
    white-space: nowrap;
  }
  .presenter {
    top: 14px;
    font-weight: 700;
    font-size: 29px;
    line-height: 30px;
    color: var(--muted);
    letter-spacing: -0.01em;
  }
  .brand-mark {
    position: absolute;
    left: 233px;
    top: 210px;
    width: 360px;
    height: 360px;
  }
  .event-name {
    top: 672px;
    font-family: "Raleway", "Helvetica Neue", sans-serif;
    font-weight: 300;
    font-size: 62px;
    line-height: 70px;
    letter-spacing: 0.2em;
    padding-left: 0.2em;
    box-sizing: border-box;
    color: var(--white);
  }
  .tagline {
    top: 784px;
    font-weight: 700;
    font-size: 32px;
    line-height: 36px;
    letter-spacing: -0.01em;
  }
  .headline {
    top: 828px;
    font-weight: 700;
    font-size: 51px;
    line-height: 56px;
    letter-spacing: -0.01em;
  }
  .divider {
    position: absolute;
    left: 120px;
    top: 906px;
    width: 614px;
    height: 2px;
    background: var(--white);
  }
  .date {
    top: 940px;
    font-weight: 400;
    font-size: 30px;
    line-height: 34px;
    color: var(--soft-white);
  }
  .access {
    top: 981px;
    font-weight: 700;
    font-size: 30px;
    line-height: 34px;
    letter-spacing: 0.04em;
  }
  .location-note {
    top: 1062px;
    font-weight: 700;
    font-size: 14px;
    line-height: 18px;
    text-transform: none;
  }
  .host-sign {
    position: absolute;
    left: 0;
    top: 1124px;
    width: 100%;
    display: flex;
    justify-content: center;
    align-items: center;
    gap: 16px;
  }
  .host-dot {
    width: 34px;
    height: 34px;
    border-radius: 50%;
    background: var(--soft-white);
  }
  .host-name {
    font-weight: 400;
    font-size: 30px;
    line-height: 34px;
    letter-spacing: 0.04em;
    text-transform: uppercase;
    color: var(--soft-white);
  }
</style>
</head>
<body>
  <main class="flyer">
    <div class="backdrop" role="img" aria-label="Dark background with diagonal silver pinstripes curving into a floor"></div>

    <p class="line-text presenter">Velvetroll Atlanta<br>Presents</p>

    <svg class="brand-mark" viewBox="0 0 360 360" aria-hidden="true">
      <defs>
        <radialGradient id="markShade" cx="50%" cy="40%" r="60%">
          <stop offset="0%" stop-color="#4a4a4a"/>
          <stop offset="100%" stop-color="#2a2a2a"/>
        </radialGradient>
      </defs>
      <circle cx="180" cy="180" r="178" fill="url(#markShade)"/>
    </svg>

    <h1 class="line-text event-name">Lantern</h1>

    <p class="line-text tagline">A Popup Nightclub Experience</p>
    <p class="line-text headline">For One Night Only</p>

    <div class="divider"></div>

    <p class="line-text date">Friday, October 18, 2013 @ 9:00 PM</p>
    <p class="line-text access">Invite Only</p>

    <p class="line-text location-note">See invitation for location details</p>

    <div class="host-sign">
      <span class="host-dot"></span>
      <span class="host-name">Velvetroll Atlanta</span>
    </div>
  </main>
</body>
</html>
```